New Wrestling company needs a website

We need a website design for a new wrestling company in Australia that will be running 3-4 events per year. Wrestling company is Summit Grip Wrestling (SGW).

The design of the logo is in place and can be provided, and I have purchased the website domain.

A detailed description of the intent and purpose of this company can be provided.

The aim would be to have around 5 specific pages on SGW, with two standard “about” and “contact” pages. E.g.
- About SGW (focus and purpose of the company)
- SGW Events (specific focus on events run by SGW)
- SGW News (news and stories on wrestling’s across Oceania)
- SGW Media (where to watch SGW and our partners))
- SGW Partners and Sponsors (partner and affiliate information)
- SGW Power Rankings (top 10 ranked wrestlers from Oceania which is updated weekly)
- SGW fans (highlighting how to become part of SGW as a fan)
- Contact SGW
Updates

The logo design should now be included in the brief, please feel free to reach out to me directly if you can't access it or require any other information.

Target Market(s)

Wrestling Fans

Industry/Entity Type

Sport / Wrestling

Coding

Coded - Design and coding required

Number of Pages Required

5+ page

Requirements
Must have
• A Wrestling and or Sports feel to the website design

```html
<!DOCTYPE html>
<html lang="en">
<head>
<meta charset="utf-8">
<title>Summit Grip Wrestling</title>
<link href="https://fonts.googleapis.com/css2?family=Michroma&family=Heebo:wght@300;400;500;600;700&display=swap" rel="stylesheet">
<style>
:root{
  --navy:#1e3a73;
  --navy-deep:#17306a;
  --topbar:#1d3468;
  --ink:#1a2a4f;
  --accent:#3b9fe0;
  --footer:#151a2b;
  --white:#ffffff;
  --grey:#6b7385;
}
*{box-sizing:border-box;margin:0;padding:0}
html,body{width:1200px;height:4732px;overflow:hidden}
body{position:relative;font-family:"Heebo",sans-serif;color:var(--ink);background:var(--white)}
.abs{position:absolute}
.display{font-family:"Michroma",sans-serif;letter-spacing:1px;font-weight:400}
.btn{position:absolute;display:flex;align-items:center;justify-content:center;font-size:14px;font-weight:600;letter-spacing:.3px;border-radius:6px}
.btn-solid{background:var(--navy);color:var(--white)}
.btn-ghost{border:2px solid var(--white);color:var(--white)}
.btn-outline{border:2px solid var(--navy);color:var(--navy);background:var(--white)}
.rule{position:absolute;height:2px;background:currentColor;opacity:.6}

.topbar{top:0;left:0;width:1200px;height:50px;background:var(--topbar);color:var(--white);font-size:14px}
.topbar .msg{left:112px;top:0;height:50px;display:flex;align-items:center;gap:14px}
.topbar .contact{right:112px;top:0;height:50px;display:flex;align-items:center;gap:28px;font-weight:500}
.topbar .contact span{display:flex;align-items:center;gap:8px}

.nav{top:50px;left:0;width:1200px;height:73px;background:var(--white)}
.brand{left:115px;top:0;height:73px;display:flex;align-items:center;gap:8px;font-weight:700;font-size:26px;color:var(--navy)}
.brand i{width:14px;height:14px;background:var(--accent);border-radius:50%}
.menu{right:112px;top:0;height:73px;display:flex;align-items:center;gap:29px;font-size:14px;font-weight:600;color:#111}

.hero{top:123px;left:0;width:1200px;height:690px;background:radial-gradient(ellipse at 72% 40%,#3a4a62 0%,#1b2233 45%,#0d111b 100%);overflow:hidden}
.hero-photo{left:560px;top:0;width:640px;height:690px;background:radial-gradient(ellipse at 55% 45%,rgba(150,110,100,.45),rgba(40,60,110,.35) 45%,rgba(0,0,0,0) 75%)}
.hero h1{left:108px;top:145px;color:var(--white);font-size:37px;line-height:56px}
.hero .btn{left:108px;top:288px;width:164px;height:57px;background:var(--navy-deep)}
.dots{left:1138px;top:243px;display:flex;flex-direction:column;gap:15px}
.dots b{width:11px;height:11px;border-radius:50%;background:var(--white)}
.dots b:first-child{background:var(--accent)}
.hero svg{left:0;top:0}

.about-halo{left:52px;top:760px;width:514px;height:514px;border-radius:50%;background:radial-gradient(circle,#fff 55%,#e9eef8 70%,#f6f8fc 88%,rgba(255,255,255,0) 100%);box-shadow:0 0 40px rgba(40,80,160,.12)}
.about-ring{left:82px;top:790px;width:454px;height:454px;border-radius:50%;border:2px solid #e3e9f4;background:#fbfcfe}
.about-photo{left:110px;top:817px;width:398px;height:398px;border-radius:50%;background:radial-gradient(circle at 50% 45%,#6a6f8a,#2a2d3c 60%,#141622)}
.about-title{left:648px;top:893px;font-size:26px;color:var(--navy)}
.about-rule{left:648px;top:938px;width:110px;color:var(--navy)}
.about-text{left:648px;top:966px;width:440px;font-size:15.5px;line-height:30px;color:#333;text-align:justify}
.about .btn{left:648px;top:1143px;width:162px;height:53px}

.events{top:1323px;left:0;width:1200px;height:833px;background:linear-gradient(180deg,#213f7c,#1c3670);color:var(--white)}
.section-title{left:0;width:1200px;text-align:center;font-size:26px}
.events .section-title{top:74px}
.center-rule{left:548px;width:104px}
.event{left:128px;width:944px;height:151px;background:var(--white);border-radius:6px;color:var(--ink)}
.team{top:0;height:151px;display:flex;align-items:center;gap:6px;font-weight:700;font-size:26px;color:var(--navy)}
.team i{width:12px;height:12px;background:var(--accent);border-radius:50%}
.team.a{left:38px}
.team.b{left:212px;color:var(--grey)}
.team.c{left:38px;color:var(--grey)}
.event .vs{left:164px;top:0;height:151px;display:flex;align-items:center;font-size:22px;font-weight:700;color:#777}
.event .meta{left:368px;top:30px;font-size:15px;color:#222}
.event .venue{left:368px;top:62px;font-size:19px;color:#111}
.event .date{left:368px;top:100px;font-size:15px;color:#222}
.event .buy{left:740px;top:20px;width:162px;height:52px}
.event .watch{left:740px;top:78px;width:162px;height:55px}
.events .load{left:518px;top:707px;width:164px;height:57px;background:var(--navy-deep)}

.ranking{top:2156px;left:0;width:1200px;height:860px;background:linear-gradient(160deg,#f6f8fb,#e9eef5 55%,#f4f6fa)}
.ranking .section-title{top:80px;color:var(--navy)}
.rank-row{left:112px;width:563px;height:50px;border:2px solid var(--navy);border-radius:4px;background:var(--white);color:var(--navy);font-size:16px;font-weight:700}
.rank-row.top{background:var(--navy);color:var(--white)}
.rank-row span{position:absolute;top:0;line-height:46px}
.rank-row .n{left:36px;width:20px;text-align:center}
.rank-row .name{left:92px}
.rank-row .dash{left:356px}
.rank-row .club{left:432px;width:110px;text-align:right;font-size:18px}
.rank-row .club.other{color:var(--grey)}
.champ-photo{left:784px;top:2415px;width:304px;height:283px;border-radius:4px;background:linear-gradient(135deg,#1d3a73,#2b6ea7 70%,#3f8fc7)}
.champ-name{left:784px;top:2732px;font-size:17px;font-weight:600;color:var(--navy)}
.champ-attr{left:784px;top:2758px;font-size:14px;font-weight:500;color:#222}
.champ-rank{left:1048px;top:2738px;font-size:32px;font-weight:600;color:var(--navy)}
.champ-text{left:784px;top:2790px;width:304px;font-size:15.5px;line-height:30px;color:#333}
.link{text-decoration:underline;color:var(--accent);font-weight:600;font-size:15.5px;letter-spacing:.5px}
.champ-link{left:788px;top:2892px}

.news{top:3016px;left:0;width:1200px;height:770px;background:radial-gradient(ellipse at 50% 40%,#2c4f93,#1b3570 60%,#132a5c)}
.news .section-title{top:70px;color:var(--white)}
.news-card{top:194px;width:294px;height:378px;background:var(--white);border-radius:4px;overflow:hidden}
.news-card .photo{position:absolute;left:0;top:0;width:294px;height:190px}
.news-card .date{position:absolute;left:26px;top:214px;font-size:14px;color:#444;display:flex;align-items:center;gap:10px}
.news-card h3{position:absolute;left:26px;top:242px;width:250px;font-size:17px;line-height:29px;font-weight:500;color:#111}
.news-card .link{position:absolute;left:26px;top:322px}
.news .load{left:518px;top:641px;width:164px;height:57px;background:var(--navy-deep)}

.fans{top:3786px;left:0;width:1200px;height:946px;background:var(--white)}
.fans .art-l{left:0;top:40px;width:260px;height:360px;background:radial-gradient(ellipse,rgba(170,160,200,.28),rgba(255,255,255,0) 70%)}
.fans .art-r{left:820px;top:40px;width:380px;height:360px;background:radial-gradient(ellipse,rgba(150,170,210,.28),rgba(255,255,255,0) 70%)}
.fans .section-title{top:106px;color:var(--navy)}
.fans-text{left:0;top:172px;width:1200px;text-align:center;font-size:23px;line-height:38px;font-weight:300;color:#222}
.fans .btn{left:520px;top:291px;width:162px;height:55px}
.footer-wave{left:0;top:0}
.partners-title{left:112px;top:440px;color:var(--white);font-size:25px}
.partners-rule{left:112px;top:497px;width:155px;color:#888}
.partner{top:536px;width:165px;height:76px;background:var(--white);border-radius:3px;display:flex;align-items:center;justify-content:center}
.partner b{width:44px;height:44px;background:#c9ccd4;border-radius:50%}
.divider{left:112px;width:976px;height:1px;background:#3a4054}
.foot-menu{left:0;width:1200px;top:700px;display:flex;justify-content:center;gap:30px;color:var(--white);font-size:14px;font-weight:500}
.foot-col{top:776px;color:var(--white);font-size:16px;line-height:31px}
.foot-col strong{display:block;font-weight:500;margin-bottom:8px}
.copyright{left:0;width:1200px;top:910px;text-align:center;color:var(--white);font-size:14px}
</style>
</head>
<body>

<header class="abs topbar">
  <div class="abs msg">
    <svg width="28" height="22" viewBox="0 0 28 22" fill="none" stroke="#fff" stroke-width="1.6"><rect x="5" y="2" width="21" height="18" rx="2"/><path d="M5 6H2v12a2 2 0 0 0 3 2M9 6h13M9 10h6M9 14h6M18 10h4v4h-4z"/></svg>
    Duis aute irure dolor in reprehenderit in voluptate.
  </div>
  <div class="abs contact">
    <span><svg width="18" height="18" viewBox="0 0 24 24" fill="#fff"><path d="M6.6 10.8a15 15 0 0 0 6.6 6.6l2.2-2.2a1 1 0 0 1 1-.25 11.4 11.4 0 0 0 3.6.57 1 1 0 0 1 1 1V20a1 1 0 0 1-1 1A17 17 0 0 1 3 4a1 1 0 0 1 1-1h3.5a1 1 0 0 1 1 1c0 1.25.2 2.45.57 3.57a1 1 0 0 1-.25 1z"/></svg>+61 400 555 010</span>
    <span><svg width="18" height="18" viewBox="0 0 24 24" fill="none" stroke="#fff" stroke-width="1.6"><circle cx="12" cy="12" r="10"/><circle cx="12" cy="10" r="3.5"/><path d="M5.5 19a8 8 0 0 1 13 0"/></svg>Login</span>
  </div>
</header>

<nav class="abs nav">
  <div class="abs brand"><i></i>SGW</div>
  <div class="abs menu">
    <span>Home</span><span>About</span><span>Events</span><span>News</span><span>Media</span><span>Partners &amp; Sponsors</span><span>Power Ranking</span><span>Fans</span><span>Contact</span>
  </div>
</nav>

<section class="abs hero">
  <div class="abs hero-photo" role="img" aria-label="Wrestler lifting an opponent overhead under arena spotlights"></div>
  <h1 class="abs display">RUNNING 3-4<br>EVENTS PERYEAR</h1>
  <div class="btn btn-ghost">GET STARTED</div>
  <div class="abs dots"><b></b><b></b><b></b></div>
  <svg class="abs" width="1200" height="690" viewBox="0 0 1200 690"><path d="M0 592 C 120 520, 250 500, 420 560 C 600 625, 760 700, 900 675 C 1000 655, 1080 600, 1200 520 L1200 690 L0 690 Z" fill="#fff"/></svg>
</section>

<section class="about">
  <div class="abs about-halo"></div>
  <div class="abs about-ring"></div>
  <div class="abs about-photo" role="img" aria-label="Two wrestlers grappling in a dark arena"></div>
  <h2 class="abs display about-title">ABOUT SGW</h2>
  <div class="rule about-rule"></div>
  <p class="abs about-text">Ut enim ad minima veniam, quis nostrum exercitationem ullam corporis suscipit laboriosam, nisi ut aliquid ex ea commodi consequatur. Ut enim ad minima veniam, quis nostrum exercitationem ullam corporis suscipit laborios, nisi ut aliquid .</p>
  <div class="btn btn-solid">LEARN MORE</div>
</section>

<section class="abs events">
  <h2 class="abs display section-title">SGW EVENTS</h2>
  <div class="rule center-rule" style="top:124px"></div>

  <div class="abs event" style="top:187px">
    <div class="abs team a"><i></i>SGW</div>
    <div class="abs vs">VS</div>
    <div class="abs team b">WR01</div>
    <div class="abs meta">SGW vs WRESTLING01</div>
    <div class="abs display venue">THE LOREM STADIUM</div>
    <div class="abs date">11 JAN, 2022, 1:00PM</div>
    <div class="btn btn-solid buy">BUY TICKETS</div>
    <div class="btn btn-outline watch">WATCH STREAM</div>
  </div>

  <div class="abs event" style="top:341px">
    <div class="abs team a"><i></i>SGW</div>
    <div class="abs vs">VS</div>
    <div class="abs team b">WR02</div>
    <div class="abs meta">SGW vs WRESTLING02</div>
    <div class="abs display venue">THE LOREM STADIUM</div>
    <div class="abs date">11 JAN, 2022, 1:00PM</div>
    <div class="btn btn-solid buy">BUY TICKETS</div>
    <div class="btn btn-outline watch">WATCH STREAM</div>
  </div>

  <div class="abs event" style="top:495px">
    <div class="abs team c">WR01</div>
    <div class="abs vs">VS</div>
    <div class="abs team b">WR02</div>
    <div class="abs meta">WRESTLING01 vs WRESTLING02</div>
    <div class="abs display venue">THE LOREM STADIUM</div>
    <div class="abs date">11 JAN, 2022, 1:00PM</div>
    <div class="btn btn-solid buy">BUY TICKETS</div>
    <div class="btn btn-outline watch">WATCH STREAM</div>
  </div>

  <div class="btn btn-ghost load">LOAD MORE</div>
</section>

<section class="abs ranking">
  <h2 class="abs display section-title">SGW POWER RANKING</h2>
  <div class="rule center-rule" style="top:128px;color:var(--navy)"></div>
</section>

<div class="abs rank-row top" style="top:2343px"><span class="n">1</span><span class="name">JONY BROWN</span><span class="dash">-</span><span class="club">SGW</span></div>
<div class="abs rank-row" style="top:2401px"><span class="n">2</span><span class="name">TIM LEE</span><span class="dash">-</span><span class="club">SGW</span></div>
<div class="abs rank-row" style="top:2458px"><span class="n">3</span><span class="name">TOM R</span><span class="dash">-</span><span class="club other">WR02</span></div>
<div class="abs rank-row" style="top:2516px"><span class="n">4</span><span class="name">DEAN</span><span class="dash">-</span><span class="club">SGW</span></div>
<div class="abs rank-row" style="top:2574px"><span class="n">5</span><span class="name">JON</span><span class="dash">-</span><span class="club other">WR01</span></div>
<div class="abs rank-row" style="top:2631px"><span class="n">6</span><span class="name">JAKE J</span><span class="dash">-</span><span class="club other">WR02</span></div>
<div class="abs rank-row" style="top:2689px"><span class="n">7</span><span class="name">DANIEL</span><span class="dash">-</span><span class="club">SGW</span></div>
<div class="abs rank-row" style="top:2747px"><span class="n">8</span><span class="name">JONNY DALE</span><span class="dash">-</span><span class="club other">WR01</span></div>
<div class="abs rank-row" style="top:2804px"><span class="n">9</span><span class="name">ANDERSON</span><span class="dash">-</span><span class="club other">WR02</span></div>
<div class="abs rank-row" style="top:2862px"><span class="n">10</span><span class="name">ROCK</span><span class="dash">-</span><span class="club other">WR01</span></div>

<div class="abs champ-photo" role="img" aria-label="Top ranked wrestler in red gloves on a blue backdrop"></div>
<div class="abs champ-name">JONY BROWM</div>
<div class="abs champ-attr">ATTRBUTES +15</div>
<div class="abs champ-rank">1</div>
<p class="abs champ-text">Itaque earum rerum hic tenetu spiente delectus, ut aut reiciendis voluptatibus maiores alias.</p>
<span class="abs link champ-link">READ MORE</span>

<section class="abs news">
  <h2 class="abs display section-title">SGW NEWS</h2>
  <article class="abs news-card" style="left:112px">
    <div class="photo" role="img" aria-label="Wrestlers in red and blue singlets locked up on the mat" style="background:linear-gradient(160deg,#2e6a9c,#a8303a 55%,#1f3b7a)"></div>
    <div class="date"><svg width="18" height="18" viewBox="0 0 24 24" fill="none" stroke="#444" stroke-width="1.6"><rect x="3" y="5" width="18" height="16" rx="2"/><path d="M3 10h18M8 3v4M16 3v4"/></svg>11 JAN 2022</div>
    <h3>QUIS AUTEM VEL EUM IURE REPREHENDERIT QUI.</h3>
    <span class="link">READ MORE</span>
  </article>
  <article class="abs news-card" style="left:453px">
    <div class="photo" role="img" aria-label="Wrestler pinning an opponent on a blue mat" style="background:linear-gradient(160deg,#3a2e3a,#a8403a 50%,#2a6aa8)"></div>
    <div class="date"><svg width="18" height="18" viewBox="0 0 24 24" fill="none" stroke="#444" stroke-width="1.6"><rect x="3" y="5" width="18" height="16" rx="2"/><path d="M3 10h18M8 3v4M16 3v4"/></svg>11 JAN 2022</div>
    <h3>QUIS AUTEM VEL EUM IURE REPREHENDERIT QUI.</h3>
    <span class="link">READ MORE</span>
  </article>
  <article class="abs news-card" style="left:793px">
    <div class="photo" role="img" aria-label="Wrestler in a yellow singlet standing in an arena" style="background:linear-gradient(160deg,#b8bcc4,#c9b04a 55%,#6e7480)"></div>
    <div class="date"><svg width="18" height="18" viewBox="0 0 24 24" fill="none" stroke="#444" stroke-width="1.6"><rect x="3" y="5" width="18" height="16" rx="2"/><path d="M3 10h18M8 3v4M16 3v4"/></svg>11 JAN 2022</div>
    <h3>QUIS AUTEM VEL EUM IURE REPREHENDERIT QUI.</h3>
    <span class="link">READ MORE</span>
  </article>
  <div class="btn btn-ghost load">LOAD MORE</div>
</section>

<section class="abs fans">
  <div class="abs art-l" role="img" aria-label="Faint drawn wrestlers grappling"></div>
  <div class="abs art-r" role="img" aria-label="Faint drawn wrestlers grappling"></div>
  <h2 class="abs display section-title">SGW FANS</h2>
  <p class="abs fans-text">Now is your chance to be a part of<br>Summit Grip Wrestling family</p>
  <div class="btn btn-solid">BECOME A FAN</div>

  <svg class="abs footer-wave" width="1200" height="946" viewBox="0 0 1200 946"><path d="M0 386 C 120 470, 330 445, 600 440 C 850 436, 1060 400, 1200 320 L1200 946 L0 946 Z" fill="var(--footer)"/></svg>

  <h2 class="abs display partners-title">OUR PARTNERS</h2>
  <div class="rule partners-rule"></div>
  <div class="abs partner" style="left:112px"><b></b></div>
  <div class="abs partner" style="left:315px"><b></b></div>
  <div class="abs partner" style="left:517px"><b></b></div>
  <div class="abs partner" style="left:720px"><b></b></div>
  <div class="abs partner" style="left:922px"><b></b></div>

  <div class="abs divider" style="top:674px"></div>
  <div class="abs foot-menu"><span>Home</span><span>About</span><span>Events</span><span>News</span><span>Media</span><span>Partners &amp; Sponsors</span><span>Power Ranking</span><span>Fans</span><span>Contact</span></div>
  <div class="abs divider" style="top:750px"></div>

  <div class="abs foot-col" style="left:112px"><strong style="padding-left:33px">CALL ON</strong>+61 400 555 010</div>
  <div class="abs foot-col" style="left:400px;width:400px;text-align:center"><strong>ADDRESS</strong>Summit Grip Wrestling,<br>Address Here</div>
  <div class="abs foot-col" style="right:112px;text-align:right"><strong>SEND MESSAGE</strong>info@summitgrip.example</div>

  <div class="abs divider" style="top:886px"></div>
  <div class="abs copyright">2022 &nbsp;Summit Grip Wrestling. All Rights Reserved.</div>
</section>

</body>
</html>
```